Flyer Design Print Ad for Clothing Store

We are a modest women's clothing store. We are looking for a print ad 90*134 mm that is attention grabbing and can serve as a template for us going forward. We cannot use pictures of actual women. We need it to include our logo, store hours, physical address, website, phone number. We would use this template and change the call to action as necessary e. g. BOGO Sale, 30% off, flash sale, summer sale etc. Our colors are black and white and our fonts are Bodoni sans and Athens.

Target Market(s)

Women from teen to age 70

Industry/Entity Type

Women's clothing

Font styles to use
Other font styles liked:
• Athens, Bodoni Sans

Requirements
Must have
• Our, logo, phone number, website, address and store hours
Nice to have
• I'd like something that's not just our flat logo but something that will make someone pause to look
Should not have
• Pictures of women

```html
<!DOCTYPE html>
<html lang="en">
<head>
<meta charset="utf-8">
<title>LINENWOOD – BOGO Sale Print Ad</title>
<link rel="stylesheet" href="https://fonts.googleapis.com/css2?family=Open+Sans:wght@400;600;700;800&family=Tenor+Sans&display=swap">
<style>
  :root {
    --ink: #111820;
    --paper-light: #efe6da;
    --paper-mid: #e2d4c2;
    --paper-dark: #cdb89c;
    --white: #ffffff;
    --pattern-tone: #d3c3ae;
  }
  * { margin: 0; padding: 0; box-sizing: border-box; }
  html, body { width: 720px; height: 1200px; overflow: hidden; background: var(--paper-light); }
  .ad {
    position: relative;
    width: 720px;
    height: 1200px;
    overflow: hidden;
    font-family: "Open Sans", Arial, sans-serif;
    color: var(--ink);
  }
  .ad-art { position: absolute; inset: 0; }

  .brand {
    position: absolute;
    left: 44px;
    top: 58px;
    width: 230px;
    text-align: center;
  }
  .brand-dot {
    display: block;
    width: 70px;
    height: 70px;
    margin: 0 auto 38px;
    border: 3px solid var(--ink);
    border-radius: 50%;
  }
  .brand-name {
    font-family: "Tenor Sans", Georgia, serif;
    font-size: 27px;
    line-height: 1;
    letter-spacing: 5px;
    color: var(--ink);
  }

  .hours {
    position: absolute;
    right: 30px;
    top: 82px;
    text-align: right;
    color: var(--white);
    font-family: "Tenor Sans", Arial, sans-serif;
    font-size: 21px;
    line-height: 27px;
  }

  .offer {
    position: absolute;
    width: 720px;
    text-align: center;
    color: var(--white);
    font-family: "Tenor Sans", Arial, sans-serif;
    -webkit-text-stroke: 1.5px var(--white);
    line-height: 1;
    transform-origin: 360px 50%;
  }
  .offer-bogo { top: 386px; left: -29px; font-size: 112px; transform: scaleX(0.74); }
  .offer-sale { top: 489px; left: -10px; font-size: 112px; transform: scaleX(0.79); }
  .offer-discount { top: 616px; left: 2px; font-size: 90px; transform: rotate(-3deg) scaleX(0.86); }
  .offer-discount sup { font-size: 50px; vertical-align: 34px; margin-left: 2px; }

  .contact { position: absolute; width: 720px; text-align: center; }
  .contact-phone {
    top: 788px;
    left: 0;
    font-size: 56px;
    font-weight: 700;
    letter-spacing: 4px;
    color: var(--ink);
    text-shadow: 0 0 3px var(--white), 2px 2px 0 var(--white), -2px -2px 0 var(--white), 2px -2px 0 var(--white), -2px 2px 0 var(--white);
  }
  .contact-web {
    top: 856px;
    left: -12px;
    font-size: 32px;
    font-weight: 600;
    letter-spacing: 6.5px;
    color: var(--ink);
    text-shadow: 2px 2px 0 var(--white), -2px -2px 0 var(--white), 2px -2px 0 var(--white), -2px 2px 0 var(--white);
  }

  .address {
    position: absolute;
    left: 226px;
    width: 494px;
    top: 976px;
    text-align: center;
    color: var(--ink);
  }
  .address-he { font-size: 38px; font-weight: 400; line-height: 46px; direction: rtl; }
  .address-en { font-size: 25px; font-weight: 700; line-height: 36px; }
  .address-note { font-size: 19px; line-height: 32px; direction: rtl; }
  .address-alt { font-size: 17px; font-weight: 600; line-height: 30px; direction: rtl; }
  .address-bus { font-size: 16px; font-weight: 700; line-height: 30px; }
</style>
</head>
<body>
<main class="ad">
  <svg class="ad-art" width="720" height="1200" viewBox="0 0 720 1200">
    <defs>
      <radialGradient id="paper" cx="55%" cy="40%" r="75%">
        <stop offset="0" stop-color="#f1e9de"/>
        <stop offset="0.7" stop-color="#e6d9c8"/>
        <stop offset="1" stop-color="#cfb99c"/>
      </radialGradient>
    </defs>

    <rect class="paper-bg" width="720" height="1200" fill="url(#paper)" role="img" aria-label="Aged paper texture with faint floral damask pattern"/>
    <circle cx="560" cy="720" r="200" fill="#d8c8b3" opacity="0.35" role="img" aria-label="Faint mandala ornament"/>

    <path class="pattern-patch" d="M0 730 C90 760 160 800 165 900 L165 1163 L0 1163 Z" fill="var(--pattern-tone)" opacity="0.85" role="img" aria-label="Dense floral tile pattern panel"/>

    <path class="swoosh" d="M0 700 C70 660 150 700 260 820 C340 900 420 940 470 990 C430 1040 380 1030 330 1000 C240 940 180 900 165 960 L165 1163 L0 1163 Z" fill="var(--white)" opacity="0.28"/>

    <polygon class="hours-band" points="435,70 720,70 720,139 390,139" fill="var(--ink)"/>

    <path class="brush-circle" d="M357 255 C470 255 552 340 552 450 C552 530 520 590 470 625 L250 640 C195 600 162 530 162 450 C162 340 245 255 357 255 Z
      M230 282 L218 270 L240 278 Z M172 362 L152 352 L170 374 Z M540 520 L570 540 L545 530 Z" fill="var(--ink)"/>
    <path class="brush-circle-edge" d="M205 300 C245 264 300 246 360 248 C300 242 235 260 195 300 Z" fill="var(--ink)"/>

    <path class="brush-banner" d="M155 628 L166 615 L548 582 L560 590 L552 604 L562 620 L552 636 L564 652 L552 668 L560 682 L548 692 L160 713 L150 700 L162 686 L152 670 L164 655 L152 642 Z" fill="var(--ink)"/>
    <path class="brush-banner-edge" d="M164 621 L548 588 L545 581 L162 614 Z" fill="var(--white)" opacity="0.9"/>

    <polygon class="footer-band-shade" points="0,1163 110,1163 75,1200 0,1200" fill="#9a9a9a"/>
    <polygon class="footer-band" points="75,1200 110,1163 720,1163 720,1200" fill="var(--ink)"/>
  </svg>

  <div class="brand">
    <span class="brand-dot"></span>
    <div class="brand-name">LINENWOOD</div>
  </div>

  <div class="hours">
    <div>S-Th - 10:00-13:00 <span dir="rtl">א-ה</span></div>
    <div>19:00 - 22:00</div>
  </div>

  <div class="offer offer-bogo">BOGO</div>
  <div class="offer offer-sale">SALE</div>
  <div class="offer offer-discount">30%<sup>OFF</sup></div>

  <div class="contact contact-phone">077-5550123</div>
  <div class="contact contact-web">www.linenwood.co.il</div>

  <div class="address">
    <div class="address-he">מרכז מסחרי גבעת ארזים</div>
    <div class="address-en">Cedar Hill Shopping Center</div>
    <div class="address-note">(מעל קפה לילך)</div>
    <div class="address-alt">ניתן להגיע גם משדרות הארזים 16</div>
    <div class="address-bus">Buses 14, 18, 23, 30, 47, 51, 56, 62, 71, 74, 80</div>
  </div>
</main>
</body>
</html>
```